IT Company requires new Business Card design.

Over the years we have had a few different business card designs. We are now due for new cards across the board for all staff. We felt this would be a good time to start fresh with a new design. Our traditional card simply had our details on the front, and a list of services on the back. We don't particularly need the list of services, we have had cards where the only thing on the rear of the card was our logo.
Feel free to be creative, we would like our tag line "Complete IT Management" to appear at some point, doesn't necessarily have to be with the logo.
I have attached samples and drafts of various previous cards we have used over the years.

```html
<!DOCTYPE html>
<html lang="en">
<head>
<meta charset="utf-8">
<title>Shoreline Tech – Business Card</title>
<link rel="stylesheet" href="https://fonts.googleapis.com/css2?family=Open+Sans:wght@400;700&display=swap">
<style>
  :root {
    --backdrop: #5a3b28;
    --card-white: #ffffff;
    --slate: #5f7180;
    --slate-text: #4f5a63;
    --on-slate: #ffffff;
  }
  * { margin: 0; padding: 0; box-sizing: border-box; }
  html, body {
    width: 1034px;
    height: 1200px;
    overflow: hidden;
  }
  body {
    background: var(--backdrop);
    font-family: "Open Sans", Arial, sans-serif;
    position: relative;
  }
  .card {
    position: absolute;
    left: 74px;
    width: 900px;
    height: 515px;
  }
  .card--front { top: 65px; background: var(--card-white); }
  .card--back { top: 626px; background: var(--slate); }

  .brand {
    position: absolute;
    left: 0; right: 0;
    top: 92px;
    display: flex;
    justify-content: center;
    align-items: center;
    gap: 22px;
  }
  .brand__square {
    width: 74px;
    height: 74px;
    background: var(--slate);
  }
  .brand__name {
    font-weight: 700;
    font-size: 64px;
    letter-spacing: 1px;
    color: var(--slate);
    text-transform: uppercase;
    line-height: 1;
  }

  .contact {
    position: absolute;
    left: 0; right: 0;
    top: 326px;
    text-align: center;
    color: var(--slate-text);
  }
  .contact__person {
    font-size: 20px;
    margin-bottom: 22px;
  }
  .contact__name {
    font-weight: 700;
    font-size: 23px;
    color: var(--slate);
  }
  .contact__row {
    display: flex;
    justify-content: center;
    align-items: center;
    gap: 18px;
    font-size: 20px;
    line-height: 1;
    margin-bottom: 20px;
  }
  .contact__item {
    display: inline-flex;
    align-items: center;
    gap: 8px;
  }
  .icon {
    width: 18px;
    height: 18px;
    fill: var(--slate-text);
  }

  .back-brand {
    position: absolute;
    left: 0; right: 0;
    top: 180px;
    text-align: center;
    font-weight: 700;
    font-size: 84px;
    line-height: 1;
    color: var(--on-slate);
    text-transform: uppercase;
    letter-spacing: 2px;
  }
  .tagline {
    position: absolute;
    left: 0; right: 0;
    top: 452px;
    text-align: center;
    font-size: 23px;
    letter-spacing: 5px;
    color: var(--on-slate);
    text-transform: uppercase;
  }
</style>
</head>
<body>
  <section class="card card--front">
    <div class="brand">
      <span class="brand__square"></span>
      <span class="brand__name">Shoreline Tech</span>
    </div>

    <div class="contact">
      <p class="contact__person"><span class="contact__name">Daniel Reeve,</span> Operation Manager</p>

      <div class="contact__row">
        <span class="contact__item">
          <svg class="icon" viewBox="0 0 24 24" aria-hidden="true"><path d="M6.6 10.8c1.4 2.8 3.8 5.1 6.6 6.6l2.2-2.2c.3-.3.7-.4 1-.2 1.1.4 2.3.6 3.6.6.6 0 1 .4 1 1V20c0 .6-.4 1-1 1C10.6 21 3 13.4 3 4c0-.6.4-1 1-1h3.5c.6 0 1 .4 1 1 0 1.3.2 2.5.6 3.6.1.3 0 .7-.2 1z"/></svg>
          08 5550 1420
        </span>
        <span class="contact__item">
          <svg class="icon" viewBox="0 0 24 24" aria-hidden="true"><path d="M7 1h10c1.1 0 2 .9 2 2v18c0 1.1-.9 2-2 2H7c-1.1 0-2-.9-2-2V3c0-1.1.9-2 2-2zm0 3v12h10V4H7zm5 14.5a1.3 1.3 0 100 2.6 1.3 1.3 0 000-2.6z"/></svg>
          0400 555 817
        </span>
        <span class="contact__item">
          <svg class="icon" viewBox="0 0 24 24" aria-hidden="true"><path d="M6 2h10l2 2v5H6V2zm-3 8h18c1.1 0 2 .9 2 2v7h-4v3H5v-3H1v-7c0-1.1.9-2 2-2zm4 7v3h10v-3H7z"/></svg>
          08 5550 1420
        </span>
      </div>

      <div class="contact__row">
        <span class="contact__item">
          <svg class="icon" viewBox="0 0 24 24" aria-hidden="true"><path d="M2 5h20v14H2V5zm2 2v.5l8 5 8-5V7H4z"/></svg>
          daniel@shorelinetech.com.au
        </span>
        <span class="contact__item">
          <svg class="icon" viewBox="0 0 24 24" aria-hidden="true"><path d="M12 2a10 10 0 100 20 10 10 0 000-20zm6.9 9h-3a15 15 0 00-1.3-5.6A8 8 0 0118.9 11zM12 4c.9 1.2 1.8 3.6 1.9 7h-3.8c.1-3.4 1-5.8 1.9-7zM9.4 5.4A15 15 0 008.1 11h-3a8 8 0 014.3-5.6zM5.1 13h3a15 15 0 001.3 5.6A8 8 0 015.1 13zM12 20c-.9-1.2-1.8-3.6-1.9-7h3.8c-.1 3.4-1 5.8-1.9 7zm2.6-1.4a15 15 0 001.3-5.6h3a8 8 0 01-4.3 5.6z"/></svg>
          www.shorelinetech.com.au
        </span>
      </div>

      <div class="contact__row">
        <span class="contact__item">Unit 4 12 Harbour Lane, Marlow WA 6100</span>
      </div>
    </div>
  </section>

  <section class="card card--back">
    <p class="back-brand">Shoreline Tech</p>
    <p class="tagline">Complete IT Management</p>
  </section>
</body>
</html>
```